Marlow Vale Stud website

We would like to create a horse stud/agistment farm website similar to this websites we have attached below:
www.thornbeck.com.au
www.quillstead.com.au
www.brackley.com
www.pimsey.com.au
The main colour scheme are purple and white to align with the stable's racing colours.
We have also attach the company logo and also images of the farm and create some ideas for the website.
Many thanks for looking into this project!

```html
<!DOCTYPE html>
<html lang="en">
<head>
<meta charset="utf-8">
<title>Marlow Vale Stud</title>
<link rel="stylesheet" href="https://fonts.googleapis.com/css2?family=Poppins:wght@400;500;600&family=Open+Sans:wght@400;600&display=swap">
<style>
:root{
  --purple:#4a1466;
  --purple-deep:#2a0a3c;
  --purple-mid:#5e1f80;
  --ink:#222;
  --body:#555;
  --muted:#888;
  --white:#fff;
  --night:#0d0d10;
}
*{box-sizing:border-box;margin:0;padding:0}
html,body{width:1200px;height:4284px;overflow:hidden;background:var(--white)}
body{font-family:"Open Sans",Arial,sans-serif;color:var(--body)}
.page{position:relative;width:1200px;height:4284px;overflow:hidden}
.abs{position:absolute}
h1,h2,h3,.nav,.brand{font-family:"Poppins",Arial,sans-serif}

/* header */
.site-header{left:0;top:0;width:1200px;height:152px;background:var(--white)}
.brand{left:86px;top:36px;display:flex;align-items:center;gap:16px;font-weight:600;font-size:30px;color:var(--purple)}
.brand-dot{width:76px;height:76px;border-radius:50%;background:var(--purple)}
.phone{left:730px;top:40px;display:flex;align-items:center;gap:10px;font-size:17px;color:var(--ink)}
.phone-icon{width:26px;height:26px;border-radius:50%;background:var(--purple);display:flex;align-items:center;justify-content:center}
.search{left:916px;top:36px;width:192px;height:32px;border:1px solid #bbb;border-radius:4px;font-size:14px;color:var(--muted);padding:6px 10px}
.search svg{position:absolute;right:9px;top:8px}
.nav{left:480px;top:92px;display:flex;gap:46px;font-size:18px;color:var(--ink)}

/* hero */
.hero{left:0;top:152px;width:1200px;height:640px;background:linear-gradient(180deg,#7aa6d6 0%,#b9cfe6 38%,#5b4a3a 60%,#5d8a3c 82%,#3d6a28 100%)}
.hero-title{left:0;top:582px;width:1200px;text-align:center;color:var(--white);font-weight:500;font-size:66px;line-height:1.1}
.hero-sub{left:0;top:676px;width:1200px;text-align:center;color:var(--white);font-size:34px;line-height:1.2;font-family:"Poppins",Arial,sans-serif}

.section-title{left:0;width:1200px;text-align:center;font-weight:500;font-size:42px;line-height:1.2;color:var(--ink)}

/* services */
.service{top:904px;width:300px;text-align:center}
.service-photo{width:212px;height:212px;border-radius:50%;margin:0 auto;border:4px solid var(--purple)}
.service h3{margin-top:26px;font-size:20px;font-weight:500;color:var(--ink)}
.service p{margin:10px auto 0;width:250px;font-size:14px;line-height:1.55}
.svc-arrow{top:990px}

/* about */
.about-band{left:0;top:1240px;width:1200px;height:960px}
.about-title{color:var(--white)}
.about-text{left:210px;top:1548px;width:780px;text-align:center;color:#e6d9ee;font-size:15px;line-height:1.75}
.video{left:248px;top:1690px;width:704px;height:400px;background:linear-gradient(180deg,#3a2a1a 0%,#6a5a48 30%,#9a8a70 55%,#c97a5a 75%,#4c6a3a 100%);box-shadow:0 8px 18px rgba(0,0,0,.35)}
.play{left:568px;top:1858px;width:64px;height:64px;border-radius:50%;background:rgba(0,0,0,.55);display:flex;align-items:center;justify-content:center}

/* farm cards */
.farm-card{top:2340px;width:472px;height:472px;background:var(--white);box-shadow:0 2px 12px rgba(0,0,0,.2);text-align:center}
.farm-photo{width:472px;height:252px}
.farm-card h3{margin-top:34px;font-size:21px;font-weight:500;color:var(--ink)}
.farm-card p{margin:12px auto 0;width:380px;font-size:14px;line-height:1.55}
.btn{display:inline-block;margin-top:18px;padding:8px 24px;border-radius:18px;background:var(--purple-deep);color:var(--white);font-size:14px;font-family:"Open Sans",Arial,sans-serif}

/* news */
.news-band{left:0;top:2860px;width:1200px;height:300px}
.news-card{top:3148px;width:296px;height:272px;background:var(--white);box-shadow:0 2px 12px rgba(0,0,0,.2);text-align:center;padding-top:22px}
.news-date{font-size:13px;color:var(--muted)}
.news-card h3{margin:12px auto 0;width:240px;font-size:19px;font-weight:500;line-height:1.35;color:var(--ink)}
.news-card p{margin:10px auto 0;width:240px;font-size:13px;line-height:1.5}
.news-card .btn{margin-top:14px}

/* contact */
.night{left:0;top:3840px;width:1200px;height:444px}
.contact-box{left:132px;top:3688px;width:936px;height:472px;background:var(--white);box-shadow:0 2px 14px rgba(0,0,0,.25);display:flex}
.contact-form{width:450px;padding:30px 48px}
.contact-form h3{font-size:24px;font-weight:500;color:var(--ink);margin-bottom:20px}
.field{height:40px;border:1px solid #ccc;margin-bottom:12px;font-size:13px;color:var(--muted);padding:10px 12px;width:330px}
.field.message{height:84px}
.send{display:inline-block;margin-top:12px;padding:8px 26px;border-radius:18px;background:var(--purple-deep);color:var(--white);font-size:14px}
.map{position:relative;width:486px;height:472px;background:linear-gradient(135deg,#e9e9e9,#d8d8d8)}
.map svg{position:absolute;left:222px;top:190px}
.socials{left:0;top:4174px;width:1200px;display:flex;justify-content:center;gap:16px}
.social{width:40px;height:40px;border-radius:50%;border:2px solid #777}
.copyright{left:0;top:4230px;width:1200px;text-align:center;font-size:13px;color:#aaa}
</style>
</head>
<body>
<div class="page">

  <header class="site-header abs">
    <div class="brand abs"><span class="brand-dot"></span>Marlow Vale Stud</div>
    <div class="phone abs">
      <span class="phone-icon"><svg width="14" height="14" viewBox="0 0 24 24"><path fill="#fff" d="M6.6 10.8a15 15 0 0 0 6.6 6.6l2.2-2.2c.3-.3.7-.4 1-.2 1.1.4 2.3.6 3.6.6.6 0 1 .4 1 1V20c0 .6-.4 1-1 1A17 17 0 0 1 3 4c0-.6.4-1 1-1h3.5c.6 0 1 .4 1 1 0 1.3.2 2.5.6 3.6.1.3 0 .7-.2 1z"/></svg></span>
      800-555-0142
    </div>
    <div class="search abs">Search
      <svg width="14" height="14" viewBox="0 0 24 24"><circle cx="10" cy="10" r="7" fill="none" stroke="#333" stroke-width="2.5"/><path d="M15 15l6 6" stroke="#333" stroke-width="2.5"/></svg>
    </div>
    <nav class="nav abs"><span>Home</span><span>About us</span><span>Services</span><span>Farms</span><span>Blog</span><span>Contact us</span></nav>
  </header>

  <section class="hero abs" role="img" aria-label="Photo of young horses standing in a green paddock under a blue sky"></section>
  <svg class="abs" style="left:1106px;top:420px" width="24" height="24" viewBox="0 0 24 24"><path d="M8 4l8 8-8 8" fill="none" stroke="#fff" stroke-width="3"/></svg>
  <h1 class="hero-title abs">Marlow Vale Stud</h1>
  <div class="hero-sub abs">Horse stud / Agistment farm</div>
  <svg class="abs" style="left:0;top:690px" width="1200" height="110" viewBox="0 0 1200 110">
    <path d="M0 34 Q600 126 1200 34 V110 H0Z" fill="#fff"/>
    <path d="M200 58 Q600 118 1000 58" fill="none" stroke="#4a1466" stroke-width="7"/>
  </svg>

  <h2 class="section-title abs" style="top:788px">Our Services</h2>
  <svg class="abs svc-arrow" style="left:56px" width="22" height="22" viewBox="0 0 24 24"><path d="M22 12H3M10 5l-7 7 7 7" fill="none" stroke="#444" stroke-width="2.5"/></svg>
  <svg class="abs svc-arrow" style="left:1122px" width="22" height="22" viewBox="0 0 24 24"><path d="M2 12h19M14 5l7 7-7 7" fill="none" stroke="#444" stroke-width="2.5"/></svg>
  <div class="service abs" style="left:102px">
    <div class="service-photo" role="img" aria-label="Photo of a grey stallion's head in a stable" style="background:radial-gradient(circle,#d9d4cc,#8a7a66)"></div>
    <h3>Silver Lantern (USA)</h3>
    <p>Silver Lantern (USA), double-dilute thoroughbred stallion, proven sire of palomino or buckskin.</p>
  </div>
  <div class="service abs" style="left:462px">
    <div class="service-photo" role="img" aria-label="Photo of a pale horse in an arena" style="background:radial-gradient(circle,#e7dcc6,#8f8a6a)"></div>
    <h3>Facility hire</h3>
    <p>Indoor arena, outdoor arena and several sized rubber lined round yards, both indoor</p>
  </div>
  <div class="service abs" style="left:822px">
    <div class="service-photo" role="img" aria-label="Photo of a bay mare and foal in a paddock" style="background:radial-gradient(circle,#b48658,#4f6a34)"></div>
    <h3>Agistment</h3>
    <p>All agistment services are on offer and can be shaped to your horse's needs</p>
  </div>

  <svg class="about-band abs" width="1200" height="960" viewBox="0 0 1200 960">
    <defs><linearGradient id="aboutFill" x1="0" y1="0" x2="0" y2="1"><stop offset="0" stop-color="#5a1d7c"/><stop offset="1" stop-color="#2a0a3c"/></linearGradient></defs>
    <path d="M0 30 Q600 190 1200 30 V950 Q600 830 0 950Z" fill="url(#aboutFill)"/>
  </svg>
  <h2 class="section-title about-title abs" style="top:1474px">About us</h2>
  <p class="about-text abs">Marlow Vale is a family run stud with a long history of breeding and caring for fine horses. Our team looks after every mare, foal and stallion as if each one were our own, with daily checks, good feed and wide paddocks. We welcome owners to visit at any time, meet the staff and see the grounds, the yards and the stables for themselves before they choose to stay.</p>
  <div class="video abs" role="img" aria-label="Video still of a racehorse and jockey in purple silks galloping past flower beds"></div>
  <div class="play abs"><svg width="26" height="26" viewBox="0 0 24 24"><path d="M7 4l13 8-13 8z" fill="#fff"/></svg></div>

  <h2 class="section-title abs" style="top:2222px">Agistment Farm</h2>
  <div class="farm-card abs" style="left:108px">
    <div class="farm-photo" role="img" aria-label="Aerial photo of farm buildings and green paddocks" style="background:linear-gradient(180deg,#8aa3b8,#5f7a48 40%,#7c8a5a 70%,#a59c7e)"></div>
    <h3>Neque porro quisquam</h3>
    <p>Wide paddocks with fresh water and shade trees, checked by our staff morning and night.</p>
    <span class="btn">View More</span>
  </div>
  <div class="farm-card abs" style="left:624px">
    <div class="farm-photo" role="img" aria-label="Photo of a timber fence and paddock at sunset" style="background:linear-gradient(180deg,#3c4a6a,#c9a07a 40%,#4a5a34 65%,#2e3a22)"></div>
    <h3>Dolorem ipsum quia dolor</h3>
    <p>Secure timber fencing and well kept yards give every horse a safe and quiet place to rest.</p>
    <span class="btn">View More</span>
  </div>

  <svg class="news-band abs" width="1200" height="300" viewBox="0 0 1200 300">
    <defs><linearGradient id="newsFill" x1="0" y1="0" x2="0" y2="1"><stop offset="0" stop-color="#5a1d7c"/><stop offset="1" stop-color="#2a0a3c"/></linearGradient></defs>
    <path d="M0 0 Q600 120 1200 0 V290 Q600 70 0 290Z" fill="url(#newsFill)"/>
  </svg>
  <h2 class="section-title abs" style="top:3048px">Latest News</h2>
  <div class="news-card abs" style="left:128px">
    <div class="news-date">JAN 29,2019</div>
    <h3>Neque porro quisquam est qui dolorem</h3>
    <p>New foals arrived this month and are settling well with their mares in the home paddock.</p>
    <span class="btn">Read More</span>
  </div>
  <div class="news-card abs" style="left:452px">
    <div class="news-date">JAN 29,2019</div>
    <h3>Neque porro quisquam est qui dolorem</h3>
    <p>Our indoor arena has a new surface and is now open for hire on weekday mornings.</p>
    <span class="btn">Read More</span>
  </div>
  <div class="news-card abs" style="left:776px">
    <div class="news-date">JAN 29,2019</div>
    <h3>Neque porro quisquam est qui dolorem</h3>
    <p>Spring open day is set for March, with farm tours, yard visits and a talk from our vet.</p>
    <span class="btn">Read More</span>
  </div>

  <h2 class="section-title abs" style="top:3588px">Contact us</h2>
  <svg class="night abs" width="1200" height="444" viewBox="0 0 1200 444">
    <path d="M0 0 Q600 260 1200 0 V444 H0Z" fill="#0d0d10"/>
  </svg>
  <div class="contact-box abs">
    <div class="contact-form">
      <h3>Quick Contact</h3>
      <div class="field">Name</div>
      <div class="field">Phone number</div>
      <div class="field">Email address</div>
      <div class="field message">Message</div>
      <span class="send">SEND</span>
    </div>
    <div class="map" role="img" aria-label="Street map showing the farm location">
      <svg width="40" height="54" viewBox="0 0 24 32"><path d="M12 0C5.4 0 0 5.4 0 12c0 9 12 20 12 20s12-11 12-20C24 5.4 18.6 0 12 0z" fill="#e53935"/><circle cx="12" cy="12" r="4.5" fill="#fff"/></svg>
    </div>
  </div>

  <div class="socials abs">
    <span class="social"></span><span class="social"></span><span class="social"></span><span class="social"></span><span class="social"></span>
  </div>
  <div class="copyright abs">Copyright © 2019. All Rights Reserved</div>

</div>
</body>
</html>
```